Stationery for Villa Marenta Design Hotel**

Who we are:

Wander on an isolated beach while breathing in the fresh, salty, sea air. Listen to the warm Pacific wind rustling through green palm trees as you walk to a pristine lagoon. Feel the delicious warmth of the sun kiss your skin; the beach is yours. At Villa Marenta you can experience a vacation in undisturbed, natural beauty. We have created a place for you to find new strength, relaxation, and inner harmony. We offer total rest to the experienced traveler from all over the world.

We are a brand new and smartly built design-hotel (under construction) close to a unique beach and a fantastic surf spot in Huatulco, Southwest Mexico.

As you can see in the attachments, we do have an established corporate design, but as for now still need a format for booklets for information around our hotel and things to do in the area, important numbers (we fill in the content for that one).

Our corporate colors:
green #64b445, brown #b07043, blue #0ab7cf, yellow # f9b02a and #fcc01a, navy #444f69
Corporate fonts:
Krub and Miller Banner.
For further information access:
www.villamarenta.example
https://slidevault.example/view/QmPxLwZrTyKsNbVcHdJe/

Social Media: VillaMarenta

Industry/Entity Type

Hotel

Font styles to use
Other font styles liked:
• Krub, Miller Banner

Requirements
Must have
• Stick to Logo Design, defined corporate elements, logo, colors, fonts and general touch and feel
Nice to have
• Who we are:

Our corporate colors:
Corporate fonts:
Krub and Miller Banner.
www.villamarenta.example

Social Media: VillaMarenta

```html
<!DOCTYPE html>
<html lang="en">
<head>
<meta charset="utf-8">
<title>Villa Marenta – Receipt</title>
<link href="https://fonts.googleapis.com/css2?family=Old+Standard+TT:wght@400;700&display=swap" rel="stylesheet">
<style>
  :root{
    --page-bg:#ececec;
    --paper:#ffffff;
    --ink:#2b2b2b;
    --muted:#7a7a7a;
    --gold:#e3a126;
    --teal-light:#2fb3c2;
    --teal-dark:#0f7f86;
    --rule:#333333;
  }
  html,body{margin:0;padding:0;overflow:hidden;}
  body{width:960px;height:1200px;background:var(--page-bg);position:relative;font-family:"Old Standard TT",Georgia,serif;color:var(--ink);}
  .receipt{position:absolute;left:94px;top:84px;width:774px;height:1030px;background:var(--paper);box-shadow:4px 4px 6px rgba(0,0,0,.25);}
  .abs{position:absolute;}
  .brand{left:46px;top:64px;width:144px;display:flex;flex-direction:column;align-items:center;gap:14px;}
  .brand-mark{width:64px;height:64px;background:var(--gold);}
  .brand-name{font-size:21px;line-height:24px;color:var(--gold);white-space:nowrap;}
  .contact{left:212px;top:52px;margin:0;padding:0;list-style:none;font-size:19px;color:var(--muted);}
  .contact li{display:flex;align-items:flex-start;height:31px;white-space:nowrap;}
  .contact svg{width:15px;height:15px;margin:5px 9px 0 0;flex:none;}
  .contact .indent{padding-left:24px;}
  .serial{left:518px;top:104px;font-size:34px;}
  .title{left:232px;top:250px;width:308px;height:54px;border-radius:16px;background:linear-gradient(180deg,var(--teal-light),var(--teal-dark));color:#fff;font-size:51px;line-height:56px;text-align:center;letter-spacing:1px;}
  .label{left:46px;font-size:42px;line-height:49px;}
  .field{left:172px;width:577px;height:45px;border:2px solid var(--rule);}
  .field.short{left:222px;width:527px;}
  .sign{font-size:42px;}
</style>
</head>
<body>
<div class="receipt">
  <div class="brand abs"><span class="brand-mark"></span><span class="brand-name">Villa Marenta</span></div>

  <ul class="contact abs">
    <li><svg viewBox="0 0 16 16"><rect x="1" y="1" width="14" height="14" rx="2" fill="var(--gold)"/><circle cx="8" cy="7" r="3" fill="#fff"/></svg>Villa Marenta, Playa Serena,</li>
    <li class="indent">Huatulco, Oaxaca, Mexiko</li>
    <li><svg viewBox="0 0 16 16"><rect x="1" y="1" width="14" height="14" rx="2" fill="var(--gold)"/><path d="M5 4l2 2-1 1.5c.7 1.3 1.5 2.1 2.5 2.5L10 9l2 2-1.5 1.5C7 12 4 9 3.5 5.5z" fill="#fff"/></svg>+52 1 (958) 555 0147</li>
    <li><svg viewBox="0 0 16 16"><rect x="1" y="3" width="14" height="10" fill="none" stroke="var(--gold)" stroke-width="1.6"/><path d="M1 3l7 6 7-6" fill="none" stroke="var(--gold)" stroke-width="1.4"/></svg>hello@villamarenta.example</li>
    <li><svg viewBox="0 0 16 16"><circle cx="8" cy="8" r="6.5" fill="none" stroke="var(--gold)" stroke-width="1.4"/><ellipse cx="8" cy="8" rx="2.8" ry="6.5" fill="none" stroke="var(--gold)" stroke-width="1.2"/><path d="M1.5 8h13M2.5 5h11M2.5 11h11" stroke="var(--gold)" stroke-width="1"/></svg>www.villamarenta.example</li>
  </ul>

  <div class="serial abs">No.</div>

  <div class="title abs">RECEIPTS</div>

  <div class="label abs" style="top:348px">Name</div>
  <div class="field abs" style="top:349px"></div>
  <div class="label abs" style="top:418px">Folio</div>
  <div class="field abs" style="top:418px"></div>
  <div class="label abs" style="top:487px">Date</div>
  <div class="field abs" style="top:487px"></div>
  <div class="label abs" style="top:556px">Room</div>
  <div class="field abs" style="top:557px"></div>
  <div class="field abs" style="top:626px"></div>
  <div class="label abs" style="top:695px">Concept</div>
  <div class="field short abs" style="top:695px"></div>
  <div class="label abs" style="top:764px">Total</div>
  <div class="field abs" style="top:764px"></div>

  <div class="sign abs" style="left:46px;top:900px">Cashier</div>
  <div class="sign abs" style="left:412px;top:892px">Guest’s Signature</div>
</div>
</body>
</html>
```